Business Card for Dental Office - "online review card"

I would like to develop a tasteful card (that would compliment my existing business card) that provides my patients a written link to a portal on my website that would facilitate the generation of online reviews.

My existing business card was a Lumaquarry project a few years ago and has been well received. I hope that it is easily accessed online for reference.

Target Market(s)

Existing patients who need guidance in accessing the "write a review" section of my website

Industry/Entity Type

Business

Requirements
Must have
• -a similar look to my existing card:
http://www.lumaquarry.com.au/contest.aspx?id=5192&page=3

-a link to the following url in writing:
http://www.tessaroldental.com/reviews.html

- a reference to "appreciating feedback" or "how are we doing?"

```html
<!DOCTYPE html>
<html lang="en">
<head>
<meta charset="utf-8">
<title>Tessarol Dental – Review Card</title>
<link href="https://fonts.googleapis.com/css2?family=Questrial&family=PT+Sans:wght@400;700&display=swap" rel="stylesheet">
<style>
  :root {
    --backdrop: #d9d9d9;
    --card: #ffffff;
    --brand-blue: #33318f;
    --brand-blue-light: #4a48a8;
    --brand-blue-dark: #2a2878;
    --name-grey: #6d6e71;
    --caption-white: #ffffff;
  }
  * { margin: 0; padding: 0; box-sizing: border-box; }
  html, body { width: 1200px; height: 725px; overflow: hidden; }
  body { background: var(--backdrop); position: relative; font-family: "PT Sans", sans-serif; }

  .card {
    position: absolute;
    width: 537px;
    height: 306px;
    background: var(--card);
    border-radius: 12px;
    overflow: hidden;
    box-shadow: 0 1px 3px rgba(0,0,0,0.25);
  }
  .card--review { left: 341px; top: 43px; }
  .card--emblem { left: 42px; top: 383px; }
  .card--signature { left: 619px; top: 383px; }

  .card__art { position: absolute; inset: 0; width: 100%; height: 100%; }

  .brand-square {
    position: absolute;
    background: var(--brand-blue);
    border-radius: 12px;
  }
  .brand-name {
    position: absolute;
    font-family: "Questrial", sans-serif;
    color: var(--name-grey);
    white-space: nowrap;
  }
  .brand-tagline {
    position: absolute;
    font-family: "Questrial", sans-serif;
    color: var(--name-grey);
    text-transform: uppercase;
    white-space: nowrap;
  }

  /* Review card */
  .card--review .brand-square { left: 38px; top: 38px; width: 75px; height: 75px; }
  .card--review .brand-name { left: 138px; top: 40px; font-size: 23px; }
  .card--review .brand-tagline { right: 124px; top: 69px; font-size: 8px; letter-spacing: 2.4px; }
  .review-caption {
    position: absolute;
    left: 0; right: 0; top: 216px;
    text-align: center;
    color: var(--caption-white);
    font-size: 20px;
    letter-spacing: 0.3px;
  }
  .review-link {
    position: absolute;
    left: 0; right: 0; top: 268px;
    text-align: center;
    color: var(--brand-blue);
    font-size: 19px;
    font-weight: 700;
  }

  /* Emblem card */
  .card--emblem .brand-square { left: 185px; top: 40px; width: 180px; height: 180px; border-radius: 22px; }
  .card--emblem .brand-name { left: 0; right: 0; top: 228px; text-align: center; font-size: 19px; }
  .card--emblem .brand-tagline { left: 0; right: 0; top: 255px; text-align: center; font-size: 7px; letter-spacing: 1.8px; }

  /* Signature card */
  .card--signature .brand-square { left: 38px; top: 117px; width: 95px; height: 95px; border-radius: 14px; }
  .card--signature .brand-name { left: 162px; top: 118px; font-size: 32px; }
  .card--signature .brand-tagline { right: 34px; top: 158px; font-size: 11px; letter-spacing: 3px; }
</style>
</head>
<body>

  <section class="card card--review">
    <svg class="card__art" viewBox="0 0 537 306" aria-hidden="true">
      <path d="M0 48 C120 70 210 135 340 112 C430 97 485 108 537 122 L537 258 L0 258 Z" fill="var(--brand-blue)"/>
      <path d="M0 160 C140 110 300 150 400 175 C460 190 505 185 537 175 L537 258 L0 258 Z" fill="var(--brand-blue-dark)" opacity="0.55"/>
      <path d="M260 150 C350 120 450 112 537 135 L537 170 C470 150 380 150 260 150 Z" fill="var(--brand-blue-light)" opacity="0.5"/>
      <rect x="28" y="-20" width="96" height="142" rx="14" fill="var(--card)"/>
    </svg>
    <div class="brand-square"></div>
    <div class="brand-name">Anne R. Tessarol, DDS</div>
    <div class="brand-tagline">And Associates</div>
    <p class="review-caption">APPRECIATING FEEDBACK</p>
    <p class="review-link">http://www.tessaroldental.com/reviews.html</p>
  </section>

  <section class="card card--emblem">
    <div class="brand-square"></div>
    <div class="brand-name">Anne R. Tessarol, DDS</div>
    <div class="brand-tagline">Family and Cosmetic Dentistry</div>
  </section>

  <section class="card card--signature">
    <div class="brand-square"></div>
    <div class="brand-name">Anne R. Tessarol, DDS</div>
    <div class="brand-tagline">And Associates</div>
  </section>

</body>
</html>
```